Premium Business Card for Wealth Creation

Please see attached business card for example.
Happy to look at options like Blue background with Yellow
Target Market(s)
People who want to buy investment property or create wealth
Industry/Entity Type
Investment
Contact Information for Business Card
Tel: 1800 314 579
Mobile: 0417 265 904
Address: Level 1, 64 Carrow Lane Brighton Vic 3186
Name: Martin Feldway
Title: CEO
Website: www.quolvane.com.au
Email: martin@quolvane.com.au
Font styles to use
Sans Serif
Colors
0255a3
fbed22
Requirements
Must have
- Look great

```html
<!DOCTYPE html>
<html lang="en">
<head>
<meta charset="utf-8">
<title>Quolvane Business Card</title>
<link rel="stylesheet" href="https://fonts.googleapis.com/css2?family=PT+Sans:wght@400;700&display=swap">
<style>
  :root {
    --stage: #d8d4cd;
    --card: #eef0f4;
    --navy: #28348a;
    --navy-deep: #1f2a78;
    --gold: #f2c12e;
    --ink-light: #eef0f8;
  }
  html, body {
    margin: 0;
    width: 1200px;
    height: 970px;
    overflow: hidden;
    background: var(--stage);
    font-family: "PT Sans", Verdana, sans-serif;
  }
  .card {
    position: absolute;
    left: 80px;
    top: 189px;
    width: 1040px;
    height: 592px;
    border-radius: 28px;
    background: var(--card);
    overflow: hidden;
    box-shadow: 0 10px 30px rgba(0,0,0,0.18);
  }
  .wave-area {
    position: absolute;
    left: 0;
    top: 270px;
    width: 1040px;
    height: 322px;
    background: linear-gradient(100deg, var(--card) 0%, var(--card) 34%, var(--navy) 57%, var(--navy-deep) 100%);
  }
  .brand {
    position: absolute;
    left: 45px;
    top: 72px;
    display: flex;
    align-items: center;
    gap: 28px;
  }
  .brand-dot {
    width: 132px;
    height: 132px;
    border-radius: 50%;
    background: var(--gold);
  }
  .brand-name {
    font-size: 92px;
    font-weight: 700;
    color: var(--navy);
    letter-spacing: 1px;
    line-height: 1;
  }
  .holder {
    position: absolute;
    left: 40px;
    top: 290px;
  }
  .holder-name {
    font-size: 37px;
    font-weight: 700;
    color: var(--navy);
    line-height: 1.1;
  }
  .holder-title {
    font-size: 26px;
    color: var(--gold);
    line-height: 1.1;
  }
  .address {
    position: absolute;
    right: 40px;
    top: 328px;
    text-align: right;
    font-size: 29px;
    line-height: 38px;
    color: var(--ink-light);
  }
  .contacts {
    position: absolute;
    right: 40px;
    top: 418px;
    list-style: none;
    margin: 0;
    padding: 0;
  }
  .contact {
    display: flex;
    justify-content: flex-end;
    align-items: center;
    gap: 12px;
    height: 34px;
    font-size: 27px;
    color: var(--ink-light);
  }
  .contact-icon {
    width: 30px;
    height: 30px;
    border-radius: 5px;
    background: var(--gold);
    display: flex;
    align-items: center;
    justify-content: center;
  }
  .contact-icon svg { width: 20px; height: 20px; }
</style>
</head>
<body>
  <div class="card">
    <div class="wave-area" role="img" aria-label="Decorative flowing band in navy and gold tones"></div>

    <div class="brand">
      <div class="brand-dot"></div>
      <div class="brand-name">QUOLVANE</div>
    </div>

    <div class="holder">
      <div class="holder-name">Martin Feldway</div>
      <div class="holder-title">CEO</div>
    </div>

    <div class="address">
      <div>Level 1, 64 Carrow Lane</div>
      <div>Elsworth Vic 3452</div>
    </div>

    <ul class="contacts">
      <li class="contact">1800 314 579
        <span class="contact-icon"><svg viewBox="0 0 20 20"><path fill="var(--navy)" d="M3,7 C3,4 7,3 10,3 C13,3 17,4 17,7 L14,8 L13,6 L7,6 L6,8Z M5,10 H15 L16,17 H4Z"/></svg></span>
      </li>
      <li class="contact">0417 265 904
        <span class="contact-icon"><svg viewBox="0 0 20 20"><rect x="6" y="2" width="8" height="16" rx="1.5" fill="var(--navy)"/><rect x="7.5" y="4" width="5" height="5" fill="var(--gold)"/></svg></span>
      </li>
      <li class="contact">martin@quolvane.com.au
        <span class="contact-icon"><svg viewBox="0 0 20 20"><rect x="3" y="5" width="14" height="10" fill="none" stroke="var(--navy)" stroke-width="1.8"/><path d="M3,5 L10,11 L17,5" fill="none" stroke="var(--navy)" stroke-width="1.8"/></svg></span>
      </li>
      <li class="contact">www.quolvane.com.au
        <span class="contact-icon"><svg viewBox="0 0 20 20"><circle cx="10" cy="10" r="7" fill="none" stroke="var(--navy)" stroke-width="1.6"/><ellipse cx="10" cy="10" rx="3" ry="7" fill="none" stroke="var(--navy)" stroke-width="1.4"/><path d="M3,10 H17" stroke="var(--navy)" stroke-width="1.4"/></svg></span>
      </li>
    </ul>
  </div>
</body>
</html>
```